Standardization and redesign of graphics for a non-fiction book

For a book project, 11 graphics need to be visually unified so that all the graphics in the book are in the same style. The graphics must be created from scratch. Just new colors aren't enough. Some of the existing graphics are by other authors who own the copyright. Accordingly, the new graphics must be truly new. This is especially true for the "2 S-curves" graphic.

Target Market(s)

Manager Furniture Industry

Industry/Entity Type

Möbel

Colors
0054AA
0677BA
7BADD7
CADEEF
E8F1F8

```html
<!DOCTYPE html>
<html lang="de">
<head>
<meta charset="utf-8">
<title>Beratungsangebote ausgewählter Schweizer Möbelhändler</title>
<link rel="stylesheet" href="https://fonts.googleapis.com/css2?family=Poppins:wght@400;600;700&display=swap">
<style>
  :root {
    --brand-blue: #0054AA;
    --mid-blue: #0677BA;
    --light-blue: #7BADD7;
    --pale-blue: #CADEEF;
    --mist-blue: #E8F1F8;
    --ink: #333333;
    --grid: #b8b8b8;
    --bg: #ffffff;
  }
  html, body {
    margin: 0;
    padding: 0;
    width: 1200px;
    height: 1200px;
    overflow: hidden;
    background: var(--bg);
  }
  .canvas {
    position: relative;
    width: 1200px;
    height: 1200px;
    font-family: "Poppins", sans-serif;
  }
  .chart-title {
    position: absolute;
    top: 382px;
    left: 0;
    width: 1200px;
    margin: 0;
    text-align: center;
    font-size: 26px;
    font-weight: 700;
    color: var(--brand-blue);
    letter-spacing: 0.1px;
  }
  .chart {
    position: absolute;
    top: 0;
    left: 0;
  }
  .axis-label { font-size: 14px; fill: var(--ink); font-weight: 400; }
  .category-label { font-size: 12px; fill: var(--ink); font-weight: 400; }
  .group-heading { font-size: 21px; fill: var(--ink); font-weight: 700; }
  .gridline { stroke: var(--grid); stroke-width: 0.8; }
</style>
</head>
<body>
<div class="canvas">
  <h1 class="chart-title">Beratungsangebote ausgewählter Schweizer Möbelhändler</h1>

  <svg class="chart" width="1200" height="1200" viewBox="0 0 1200 1200" role="img"
       aria-label="Balkendiagramm: Anzahl Händler je Beratungsangebot">
    <defs>
      <linearGradient id="frame-revenue" x1="0" y1="0" x2="0" y2="1">
        <stop offset="0" stop-color="#4aa0e8"/>
        <stop offset="1" stop-color="#0a4fb5"/>
      </linearGradient>
      <linearGradient id="frame-acquisition" x1="0" y1="0" x2="0" y2="1">
        <stop offset="0" stop-color="#30f5f5"/>
        <stop offset="1" stop-color="#1ab4e0"/>
      </linearGradient>
      <linearGradient id="bar-deep" x1="0" y1="0" x2="0" y2="1">
        <stop offset="0" stop-color="#4a9fe6"/>
        <stop offset="1" stop-color="#0047ab"/>
      </linearGradient>
      <linearGradient id="bar-sky" x1="0" y1="0" x2="0" y2="1">
        <stop offset="0" stop-color="#3ecbff"/>
        <stop offset="1" stop-color="#0677c8"/>
      </linearGradient>
      <linearGradient id="bar-cyan" x1="0" y1="0" x2="0" y2="1">
        <stop offset="0" stop-color="#2efff2"/>
        <stop offset="1" stop-color="#18b4d8"/>
      </linearGradient>
    </defs>

    <!-- group frames -->
    <rect class="group-frame" x="125" y="468" width="548.6" height="356" fill="none" stroke="url(#frame-revenue)" stroke-width="2.4"/>
    <rect class="group-frame" x="700" y="468" width="401.6" height="356" fill="none" stroke="url(#frame-acquisition)" stroke-width="2.4"/>

    <!-- y axis labels -->
    <g class="y-axis" text-anchor="middle">
      <text class="axis-label" x="104" y="474">7</text>
      <text class="axis-label" x="104" y="514">6</text>
      <text class="axis-label" x="104" y="552">5</text>
      <text class="axis-label" x="104" y="590">4</text>
      <text class="axis-label" x="104" y="628">3</text>
      <text class="axis-label" x="104" y="666">2</text>
      <text class="axis-label" x="104" y="706">1</text>
      <text class="axis-label" x="104" y="742">0</text>
    </g>

    <!-- gridlines -->
    <g class="grid">
      <line class="gridline" x1="150" y1="513" x2="265" y2="513"/>
      <line class="gridline" x1="499" y1="513" x2="948" y2="513"/>
      <line class="gridline" x1="150" y1="551" x2="1072" y2="551"/>
      <line class="gridline" x1="150" y1="589" x2="1072" y2="589"/>
      <line class="gridline" x1="150" y1="627" x2="1072" y2="627"/>
      <line class="gridline" x1="150" y1="665" x2="1072" y2="665"/>
      <line class="gridline" x1="150" y1="705" x2="1072" y2="705"/>
      <line class="gridline" x1="150" y1="741" x2="1072" y2="741"/>
    </g>

    <!-- group headings -->
    <text class="group-heading" x="385" y="514" text-anchor="middle">Umsatzabschöpfung</text>
    <text class="group-heading" x="1073" y="514" text-anchor="end">Akquisition</text>

    <!-- bars -->
    <g class="bars">
      <rect x="231.2" y="550.4" width="36.8" height="190.4" fill="url(#bar-deep)"/>
      <rect x="390.4" y="526.4" width="36.8" height="214.4" fill="url(#bar-sky)"/>
      <rect x="547.2" y="590.4" width="36.8" height="150.4" fill="url(#bar-cyan)"/>
      <rect x="833.6" y="705.6" width="36.8" height="35.2" fill="url(#bar-deep)"/>
      <rect x="978.4" y="627.2" width="36.8" height="113.6" fill="url(#bar-sky)"/>
    </g>

    <!-- category labels -->
    <g class="categories" text-anchor="middle">
      <text class="category-label" x="248" y="780">Offline Einrichtungs-</text>
      <text class="category-label" x="248" y="801">und Produktberatung</text>
      <text class="category-label" x="409" y="780">Online</text>
      <text class="category-label" x="409" y="801">Produktberatung</text>
      <text class="category-label" x="566" y="780">Online</text>
      <text class="category-label" x="566" y="801">Einrichtungsberatung</text>
      <text class="category-label" x="852" y="780">Automatisierte</text>
      <text class="category-label" x="852" y="801">Beratung</text>
      <text class="category-label" x="996" y="780">Renderings</text>
    </g>
  </svg>
</div>
</body>
</html>
```